MRT Property - Business Cards

Looking for a business card & general letterhead, signage etc design for our new logo.

Colours:
000a20
0056a2
00b5ef
0088ce
68cef2

Fonts:
Poppins
Karla

Please keep look and feel of new brand - example in the zip package I sent.

```html
<!DOCTYPE html>
<html lang="en">
<head>
<meta charset="utf-8">
<title>MRT Property – Business Cards</title>
<link href="https://fonts.googleapis.com/css2?family=Poppins:wght@400;600;700&family=Karla:wght@400;500&display=swap" rel="stylesheet">
<style>
  :root {
    --navy: #000a20;
    --card-dark: #0e1428;
    --blue: #0056a2;
    --sky: #00b5ef;
    --mid: #0088ce;
    --light: #68cef2;
    --white: #ffffff;
    --stage: #3d3d3d;
  }
  * { box-sizing: border-box; margin: 0; padding: 0; }
  html, body { width: 1200px; height: 803px; overflow: hidden; }
  body {
    background: var(--stage);
    font-family: "Karla", sans-serif;
    position: relative;
  }
  .card {
    position: absolute;
    top: 250px;
    width: 520px;
    height: 300px;
    border-radius: 18px;
    border-bottom: 3px solid var(--light);
    box-shadow: 0 18px 40px rgba(0,0,0,0.45);
    overflow: hidden;
  }
  .card-back { left: 50px; background: var(--card-dark); }
  .card-front { left: 630px; background: var(--white); }

  /* Back: contact details */
  .back-content {
    position: absolute;
    left: 34px;
    bottom: 30px;
  }
  .brand-name {
    font-family: "Poppins", sans-serif;
    font-weight: 700;
    color: var(--blue);
    line-height: 1;
  }
  .card-back .brand-name { font-size: 30px; margin-bottom: 14px; }
  .person-name {
    font-family: "Poppins", sans-serif;
    font-weight: 700;
    font-size: 19px;
    color: var(--blue);
    line-height: 1.1;
  }
  .person-role {
    font-size: 13px;
    color: var(--sky);
    margin-bottom: 12px;
  }
  .address {
    font-size: 13px;
    color: var(--white);
    line-height: 1.35;
    margin-bottom: 10px;
  }
  .contacts { list-style: none; }
  .contacts li {
    display: flex;
    align-items: center;
    gap: 8px;
    font-size: 13px;
    color: var(--white);
    line-height: 1.45;
  }
  .contacts svg { width: 11px; height: 11px; flex: none; }

  /* Front: wordmark */
  .front-mark {
    position: absolute;
    inset: 0;
    display: flex;
    align-items: center;
    justify-content: center;
    gap: 16px;
  }
  .front-mark .dot {
    width: 46px;
    height: 46px;
    border-radius: 50%;
    background: var(--sky);
  }
  .card-front .brand-name { font-size: 48px; }
</style>
</head>
<body>
  <section class="card card-back">
    <div class="back-content">
      <div class="brand-name">MRT Property</div>
      <div class="person-name">Daniel Hart</div>
      <div class="person-role">President</div>
      <div class="address">412 Cedar Ridge Road<br>Halton, Canada 20815</div>
      <ul class="contacts">
        <li>
          <svg viewBox="0 0 12 12"><path d="M2 1h3l1 3-1.5 1a7 7 0 0 0 2.5 2.5L8 6l3 1v3a1 1 0 0 1-1 1A9 9 0 0 1 1 2a1 1 0 0 1 1-1z" fill="var(--mid)"/></svg>
          555-201-4873
        </li>
        <li>
          <svg viewBox="0 0 12 12"><rect x="1.5" y="1.5" width="9" height="9" fill="none" stroke="var(--mid)" stroke-width="1.5"/></svg>
          555-309-6142
        </li>
        <li>
          <svg viewBox="0 0 12 12"><rect x="1" y="2.5" width="10" height="7" fill="var(--mid)"/><path d="M1 2.5l5 4 5-4" fill="none" stroke="var(--card-dark)" stroke-width="1"/></svg>
          info@mrtprop.com
        </li>
        <li>
          <svg viewBox="0 0 12 12"><circle cx="6" cy="6" r="5" fill="var(--mid)"/></svg>
          www.mrtprop.com
        </li>
      </ul>
    </div>
  </section>

  <section class="card card-front">
    <div class="front-mark">
      <span class="dot"></span>
      <span class="brand-name">MRT Property</span>
    </div>
  </section>
</body>
</html>
```